Holistic/ Sports Psychologist needs flyer design

I need a flyer designed that catches the attention of potential customers - (parents of young athletes and athletes) who may be looking for psychological services. I have a logo and all the relevant info for the flyer but would like someone to take it and make it look creative, fun, fresh and attention getting for high school and college athletes. The colors used can be from my logo design which represents my holistic approach.
Target Market(s)
high school and collegiate athletes
Industry/Entity Type
sports psychology
Requirements
Must have
- Info I put on the flyer with my logo and please add some graphics and color based on my logo

```html
<!DOCTYPE html>
<html lang="en">
<head>
<meta charset="utf-8">
<title>Sports Psychology Flyer – Front and Back</title>
<link href="https://fonts.googleapis.com/css2?family=Poppins:ital,wght@0,300;0,400;0,500;0,600;0,700;1,400;1,500&display=swap" rel="stylesheet">
<style>
:root{
  --stage:#adadad;
  --paper:#e2fad6;
  --forest:#4e6b42;
  --navy:#3a66a0;
  --orange:#e87722;
  --leaf:#a8d27a;
  --bubble:#c6e6bb;
  --ink:#2f2f2f;
  --white:#ffffff;
}
*{margin:0;padding:0;box-sizing:border-box}
html,body{width:1200px;height:1079px;overflow:hidden;background:var(--stage)}
body{position:relative;font-family:'Poppins',sans-serif;color:var(--ink)}
.side-label{position:absolute;top:126px;width:300px;text-align:center;color:var(--white);font-weight:400;font-size:48px;letter-spacing:1px;line-height:60px}
.side-label.front{left:179px}
.side-label.back{left:703px}
.page{position:absolute;top:215px;width:487px;height:730px;background:var(--paper);overflow:hidden}
.page.front{left:87px}
.page.back{left:611px}
.art{position:absolute;left:0;top:0;width:487px;height:730px}
.abs{position:absolute}
.brand{left:16px;top:18px;display:flex;align-items:center;gap:7px}
.brand-dot{width:36px;height:36px;border-radius:50%;background:var(--white);border:2px solid var(--navy)}
.brand-name{font-size:11.5px;color:var(--navy);font-weight:400;position:relative;padding-bottom:9px}
.brand-bar{position:absolute;left:-4px;top:19px;width:134px;height:8px;background:var(--leaf)}
.header-band{left:254px;top:5px;width:240px;height:47px;background:var(--forest);border-radius:24px 0 0 24px;color:var(--white);font-weight:600;font-size:9.6px;line-height:13px;text-align:right;padding:13px 13px 0 0}
.title-band{left:27px;top:309px;width:300px;height:47px;background:var(--forest);border-radius:24px;color:var(--white);font-weight:600;font-size:9.4px;line-height:12.5px;text-align:right;padding:11px 54px 0 0}
.tab{height:28px;border-radius:0 15px 15px 0;color:var(--white);font-weight:600;font-size:9.6px;line-height:28px;padding-left:11px;letter-spacing:.2px}
.tab.blue{background:var(--navy)}
.tab.orange{background:var(--orange)}
.checklist{list-style:none;font-size:10.8px}
.checklist li{position:absolute;left:0;display:flex;align-items:center;gap:7px;white-space:nowrap;line-height:14px}
.checklist svg{width:15px;height:15px;flex:none}
.lead{font-size:9.6px;line-height:13.6px}
.body-copy{font-size:9.1px;line-height:15.2px;text-align:justify;font-weight:400}
.telehealth{left:29px;top:431px;width:191px;height:61px;background:var(--forest);color:var(--white);text-align:center;border-radius:2px;padding-top:13px}
.telehealth .note{font-style:italic;font-size:10.2px;line-height:14px;font-weight:300}
.telehealth .word{font-weight:600;font-size:14.5px;line-height:20px;letter-spacing:.4px}
.session-pill{left:76px;top:531px;width:144px;height:39px;background:var(--orange);border:2px solid var(--white);border-radius:0 20px 20px 0;color:var(--white);padding:3px 0 0 24px}
.session-pill .k{font-weight:600;font-size:10px;line-height:14px}
.session-pill .v{font-style:italic;font-size:10.4px;line-height:14px}
.session-icon{left:20px;top:515px;width:70px;height:70px;border-radius:50%;background:var(--orange);border:3px solid var(--white);box-shadow:0 0 0 1.5px var(--orange);display:flex;align-items:center;justify-content:center}
.accent{color:var(--orange);font-weight:600;font-style:normal}
.specialties{font-style:italic}
.contact{font-size:8.6px;color:var(--white);line-height:11.5px;display:flex;align-items:center;gap:9px}
.contact .ic{width:20px;height:20px;border-radius:50%;background:var(--white);display:flex;align-items:center;justify-content:center;flex:none}
.phone-bar{left:262px;top:678px;width:225px;height:45px;background:var(--orange);color:var(--white);display:flex;align-items:center;justify-content:flex-end;gap:9px;padding-right:13px;font-weight:600;font-size:18.5px;letter-spacing:.3px}
.phone-bar .ic{width:22px;height:22px;border-radius:50%;background:var(--white);display:flex;align-items:center;justify-content:center}
</style>
</head>
<body>

<svg width="0" height="0" style="position:absolute" aria-hidden="true">
  <defs>
    <symbol id="tick-orange" viewBox="0 0 16 16"><circle cx="7.5" cy="8.5" r="6.5" fill="#e87722"/><path d="M4.3 8.6l2.4 2.4 6.6-7.2" fill="none" stroke="#fff" stroke-width="1.8" stroke-linecap="round" stroke-linejoin="round"/></symbol>
    <symbol id="tick-blue" viewBox="0 0 16 16"><circle cx="7.5" cy="8.5" r="6.5" fill="#3a66a0"/><path d="M4.3 8.6l2.4 2.4 6.6-7.2" fill="none" stroke="#fff" stroke-width="1.8" stroke-linecap="round" stroke-linejoin="round"/></symbol>
    <linearGradient id="g-group" x1="0" y1="0" x2="1" y2="1"><stop offset="0" stop-color="#9fb38a"/><stop offset=".5" stop-color="#8a8680"/><stop offset="1" stop-color="#5c5650"/></linearGradient>
    <linearGradient id="g-yoga" x1="0" y1="0" x2="0" y2="1"><stop offset="0" stop-color="#eeeae6"/><stop offset="1" stop-color="#b9b2ab"/></linearGradient>
    <linearGradient id="g-field" x1="0" y1="0" x2="1" y2="1"><stop offset="0" stop-color="#4f7a3a"/><stop offset=".6" stop-color="#3d6131"/><stop offset="1" stop-color="#2f4f8f"/></linearGradient>
    <linearGradient id="g-dusk" x1="0" y1="0" x2="0" y2="1"><stop offset="0" stop-color="#e2b08d"/><stop offset=".55" stop-color="#b58670"/><stop offset="1" stop-color="#3d2e2a"/></linearGradient>
  </defs>
</svg>

<div class="side-label front">FRONT</div>
<div class="side-label back">BACK</div>

<!-- Front page -->
<section class="page front">
  <svg class="art" viewBox="0 0 487 730" aria-hidden="false">
    <path d="M0 0H487V330H0Z" fill="#fff"/>
    <g role="img" aria-label="Photo of a group therapy session, young adults seated in a bright room">
      <path d="M0 130C80 96 205 84 244 12L250 0H487V318H300C200 300 90 292 0 206Z" fill="url(#g-group)"/>
    </g>
    <path d="M0 127C82 92 205 80 240 20" fill="none" stroke="#e87722" stroke-width="5"/>
    <path d="M0 210C90 292 200 296 300 300" fill="none" stroke="#fff" stroke-width="4"/>
    <path d="M0 218C92 300 200 304 300 306" fill="none" stroke="#e87722" stroke-width="5"/>
    <path d="M447 352L487 380V430C470 400 456 380 430 360Z" fill="#e87722"/>
    <circle cx="29" cy="275" r="17" fill="var(--bubble)"/>
    <circle cx="260" cy="396" r="17" fill="var(--bubble)"/>
    <circle cx="199" cy="487" r="17" fill="var(--bubble)"/>
    <circle cx="432" cy="553" r="17" fill="var(--bubble)"/>
    <circle cx="221" cy="693" r="17" fill="var(--bubble)"/>
    <circle cx="377" cy="315" r="90" fill="#eefbe6" stroke="#3a66a0" stroke-width="1.2"/>
    <g role="img" aria-label="Photo of a woman meditating in a seated yoga pose">
      <circle cx="377" cy="315" r="82" fill="url(#g-yoga)"/>
    </g>
  </svg>

  <div class="abs brand"><span class="brand-dot"></span><span class="brand-name">Dr. Lorelei Ashford<span class="brand-bar"></span></span></div>
  <div class="abs header-band">HOLISTIC PSYCHOLOGY AND<br>SPORTS PSYCHOLOGY CONSULTING</div>
  <div class="abs title-band">WAYS TO IMPROVE ATHLETIC PERFORMANCE<br>USING SPORTS AND HOLISTIC PSYCHOLOGY</div>

  <div class="abs tab blue" style="left:35px;top:392px;width:150px">MENTAL SKILLS TRAINING</div>
  <ul class="abs checklist" style="left:51px;top:0">
    <li style="top:433px"><svg><use href="#tick-orange"/></svg>Visualization</li>
    <li style="top:453px"><svg><use href="#tick-orange"/></svg>Goal-setting</li>
    <li style="top:477px"><svg><use href="#tick-orange"/></svg>Motivation</li>
    <li style="top:497px"><svg><use href="#tick-orange"/></svg>Self- talk</li>
    <li style="top:520px"><svg><use href="#tick-orange"/></svg>Mindset</li>
    <li style="top:542px"><svg><use href="#tick-orange"/></svg>Concentration Techniques</li>
  </ul>

  <div class="abs tab blue" style="left:35px;top:582px;width:112px">MENTAL HEALTH</div>
  <p class="abs lead" style="left:36px;top:622px;font-size:10.4px">Anxiety and Stress management by using</p>
  <ul class="abs checklist" style="left:51px;top:0">
    <li style="top:650px"><svg><use href="#tick-orange"/></svg>Relaxation Techniques</li>
    <li style="top:671px"><svg><use href="#tick-orange"/></svg>Breathwork</li>
    <li style="top:694px"><svg><use href="#tick-orange"/></svg>Mindfulness Practices</li>
  </ul>

  <div class="abs tab orange" style="left:260px;top:426px;width:177px;border-radius:15px">PERFORMANCE ENHANCEMENT</div>
  <p class="abs lead" style="left:260px;top:459px;width:200px">Eliminate psychological barriers that are hindering performance such as</p>
  <ul class="abs checklist" style="left:283px;top:0">
    <li style="top:500px"><svg><use href="#tick-blue"/></svg>Self- doubt</li>
    <li style="top:520px"><svg><use href="#tick-blue"/></svg>Perfectionism</li>
    <li style="top:544px"><svg><use href="#tick-blue"/></svg>Fear of Failure</li>
    <li style="top:564px"><svg><use href="#tick-blue"/></svg>Burnout</li>
  </ul>

  <div class="abs tab orange" style="left:261px;top:596px;width:167px;border-radius:15px">INJURY RECOVERY SUPPORT</div>
  <p class="abs body-copy" style="left:261px;top:635px;width:197px">Assist athletes in maintaining resilience and positive mental attitude during rehabilitation as well as processing emotions relating to any potential trauma caused by the injury or life transitions resulting from it.</p>
</section>

<!-- Back page -->
<section class="page back">
  <svg class="art" viewBox="0 0 487 730">
    <path d="M0 0H487V300H0Z" fill="#fff"/>
    <g role="img" aria-label="Photo of a youth soccer coach talking with young players seated on a turf field">
      <path d="M0 120C82 88 205 78 246 6L250 0H487V380L440 300C380 282 330 275 300 275C180 272 70 262 0 200Z" fill="url(#g-field)"/>
    </g>
    <path d="M0 118C84 86 205 76 240 14" fill="none" stroke="#e87722" stroke-width="5"/>
    <path d="M0 204C72 262 180 274 300 278" fill="none" stroke="#fff" stroke-width="4"/>
    <path d="M0 212C74 270 180 282 300 285" fill="none" stroke="#e87722" stroke-width="5"/>
    <path d="M449 334L487 362V428C470 398 455 378 428 350Z" fill="#e87722"/>
    <circle cx="28" cy="273" r="13" fill="var(--bubble)"/>
    <circle cx="298" cy="357" r="27" fill="var(--bubble)"/>
    <circle cx="264" cy="388" r="13" fill="var(--bubble)"/>
    <circle cx="225" cy="605" r="13" fill="var(--bubble)"/>
    <circle cx="192" cy="645" r="34" fill="var(--bubble)"/>
    <circle cx="376" cy="305" r="90" fill="#eefbe6" stroke="#3a66a0" stroke-width="1.2"/>
    <g role="img" aria-label="Photo of a person meditating on a mountain ridge at sunrise">
      <circle cx="376" cy="305" r="82" fill="url(#g-dusk)"/>
    </g>
    <path d="M0 593C130 612 240 650 311 730H0Z" fill="#4e6b42"/>
    <path d="M0 601C130 620 232 654 300 724" fill="none" stroke="#fff" stroke-width="2.5"/>
    <rect x="262" y="723" width="225" height="3" fill="#e87722"/>
  </svg>

  <div class="abs brand"><span class="brand-dot"></span><span class="brand-name">Dr. Lorelei Ashford<span class="brand-bar"></span></span></div>

  <div class="abs tab blue" style="left:30px;top:313px;width:151px;border-radius:0 15px 15px 0">BURNOUT PREVENTION</div>
  <p class="abs body-copy" style="left:30px;top:351px;width:197px">Teach athletes how to have balance in sports and life so they can experience longevity in their sports as well as overall optimal health and well-being.</p>

  <div class="abs telehealth"><div class="note">All services are provided online via</div><div class="word">TELEHEALTH.</div></div>

  <div class="abs session-pill"><div class="k">SESSIONS</div><div class="v">30 or 55 minutes.</div></div>
  <div class="abs session-icon">
    <svg width="40" height="38" viewBox="0 0 40 38" fill="none" stroke="#fff" stroke-width="2" stroke-linecap="round" stroke-linejoin="round">
      <rect x="9" y="14" width="25" height="17" rx="1.5"/>
      <path d="M5 34H38"/>
      <circle cx="21.5" cy="20" r="2.6"/>
      <path d="M16.5 28c1-3 3-4 5-4s4 1 5 4"/>
      <path d="M2 4h16v10H9l-4 3v-3H2z" fill="#e87722"/>
      <path d="M6 8h8M6 11h5"/>
    </svg>
  </div>

  <div class="abs tab orange" style="left:260px;top:418px;width:166px;border-radius:0 15px 15px 0">DR. LORELEI ASHFORD</div>
  <p class="abs body-copy" style="left:260px;top:455px;width:203px">Dr. Lorelei Ashford is a licensed psychologist. She understands the unique experiences of athletes due to her background as an All-American swimmer, collegiate and age group swim coach, parent of a collegiate/professional athlete, and sports psychology researcher. She works with athletes to optimize performance and overall well-being.</p>
  <p class="abs body-copy specialties" style="left:260px;top:597px;width:203px"><span class="accent">HER SPECIALIZATIONS INCLUDE:</span> performance anxiety, mental performance, stress management, anxiety, depressions, trauma, life transitions, relationship issues, injury, and sleep.</p>

  <div class="abs contact" style="left:27px;top:655px">
    <span class="ic"><svg width="12" height="12" viewBox="0 0 12 12" fill="none" stroke="#4e6b42" stroke-width="1"><circle cx="6" cy="6" r="5"/><path d="M1 6h10M6 1c-2.5 3-2.5 7 0 10M6 1c2.5 3 2.5 7 0 10"/></svg></span>
    <span>www.drloreleiashford.com</span>
  </div>
  <div class="abs contact" style="left:27px;top:685px">
    <span class="ic"><svg width="11" height="13" viewBox="0 0 11 13"><path d="M5.5 12.5S1 7.6 1 5a4.5 4.5 0 019 0c0 2.6-4.5 7.5-4.5 7.5z" fill="#4e6b42"/><circle cx="5.5" cy="5" r="1.6" fill="#fff"/></svg></span>
    <span>2280 Harbor Lane #104<br>Coral Bend, FL 32099</span>
  </div>

  <div class="abs phone-bar">
    <span class="ic"><svg width="13" height="13" viewBox="0 0 24 24"><path d="M6.6 10.8a15.1 15.1 0 006.6 6.6l2.2-2.2a1 1 0 011-.24 11.4 11.4 0 003.6.57 1 1 0 011 1V20a1 1 0 01-1 1A17 17 0 013 4a1 1 0 011-1h3.5a1 1 0 011 1c0 1.25.2 2.45.57 3.57a1 1 0 01-.25 1z" fill="#e87722"/></svg></span>
    <span>555-014-2290</span>
  </div>
</section>

</body>
</html>
```